Company Brochure - Recruitment Agency

We need a company brochure. We are a recruitment firm and we want to depict a professional, energetic and result oriented image. We would like our brochure to be in line with our logo design. A color filled and modern design will be a big plus.

We want the brochure to be smaller than a A4 size paper, elongated in shape with 3 pages on each side (see attached pics)
Updates

Reason: Need more designs to compare. Did not like the ones I received so far.

Target Market(s)

Big Corporations and Global Multinational companies

Industry/Entity Type

It Company

Requirements
Must have
• 6 long-sided Pages Design (with 3 Pages on each side)
• Page Measurement: 26cm x 14cm (for each page)
• Brochure Measurement: 26cm x 14 cm (when folded)
Nice to have
• Theme in line with our logo design.
• Project a fast, energetic and professional image.
Should not have
• Am open at this moment

```html
<!DOCTYPE html>
<html lang="en">
<head>
<meta charset="utf-8">
<title>SwiftTalent Consultants – Trifold Brochure</title>
<link rel="stylesheet" href="https://fonts.googleapis.com/css2?family=Questrial&family=Arimo:wght@400;700&display=swap">
<style>
  :root{
    --backdrop:#124a69;
    --green:#2e9a3c;
    --green-light:#5cbf3f;
    --green-dark:#1d7a2e;
    --paper:#ffffff;
    --paper-grey:#ececec;
    --ink:#333333;
    --ink-soft:#555555;
  }
  *{box-sizing:border-box;margin:0;padding:0}
  html,body{width:900px;height:1200px;overflow:hidden}
  body{background:var(--backdrop);font-family:"Arimo",Arial,sans-serif;color:var(--ink);position:relative}
  .spread{position:absolute;left:52px;width:798px;height:494px;background:var(--paper);overflow:hidden}
  .spread--outer{top:79px}
  .spread--inner{top:626px;height:491px}
  .panel{position:absolute;top:0;height:100%;overflow:hidden}
  .panel--a{left:0;width:265px}
  .panel--b{left:265px;width:267px}
  .panel--c{left:532px;width:266px}
  .green-fill{background:linear-gradient(160deg,var(--green-light) 0%,var(--green) 55%,var(--green-dark) 100%);color:#fff}
  .grey-fill{background:linear-gradient(90deg,#f7f7f7 0%,var(--paper-grey) 50%,#f7f7f7 100%)}
  .photo{position:absolute}
  .heading{font-family:"Questrial","Century Gothic",sans-serif;font-weight:700}
  .small{font-size:6.6px;line-height:8.4px}

  /* process panel */
  .process{position:absolute;left:8px;top:12px;width:248px;font-size:7px;line-height:8.6px}
  .process h2{font-size:12.5px;line-height:15px;border-bottom:1px solid rgba(255,255,255,.7);padding-bottom:2px;margin-bottom:4px;font-family:"Arimo",sans-serif;font-weight:700}
  .process .intro{font-weight:700;margin-bottom:8px}
  .step{display:flex;gap:5px;margin-bottom:7px}
  .step__num{flex:0 0 9px;height:9px;background:#fff;color:var(--green);font-size:6.5px;font-weight:700;text-align:center;line-height:9px}
  .step p{text-align:justify}

  /* contact panel */
  .contact{position:absolute;left:0;width:100%;top:128px;text-align:center;color:var(--ink)}
  .contact h2{font-size:16px;font-family:"Questrial",sans-serif;font-weight:700;color:#222}
  .contact .rule{width:210px;height:1px;background:var(--green);margin:3px auto 5px}
  .contact-item{font-family:"Questrial",sans-serif;font-size:12px;margin-bottom:6px}
  .contact-item svg{display:block;margin:0 auto 2px}
  .brand{font-family:"Questrial",sans-serif;font-weight:700;color:var(--green);line-height:1}
  .brand span{display:block;font-size:.33em;letter-spacing:.28em;text-align:right}
  .address{position:absolute;left:0;width:100%;top:445px;text-align:center;font-family:"Questrial",sans-serif;font-size:9px;line-height:12px;color:#333}

  /* cover panel */
  .cover-url{position:absolute;bottom:14px;width:100%;text-align:center;color:#fff;font-size:10px;font-weight:700}

  /* inner spread */
  .tag{display:inline-block;background:var(--green);color:#fff;font-weight:700;font-size:10px;padding:1px 18px 1px 5px;clip-path:polygon(0 0,100% 0,90% 100%,0 100%);margin-bottom:5px}
  .company{position:absolute;left:13px;top:16px;width:243px;line-height:8.8px}
  .company p{text-align:justify;margin-bottom:4px}
  .ticks{list-style:none}
  .ticks li{padding-left:9px;position:relative}
  .ticks li::before{content:"✓";position:absolute;left:0;font-weight:700}
  .industry{position:absolute;left:10px;top:12px;width:250px}
  .industry h2{font-size:14px;margin-bottom:6px;font-family:"Arimo",sans-serif}
  .industry .intro{margin-bottom:8px}
  .cols{display:flex;gap:12px}
  .col{flex:1}
  .col h3{font-size:10.5px;font-weight:700;margin:0 0 2px}
  .col ul{list-style:none;margin-bottom:8px}
  .col li::before{content:"• "}
  .col li{font-size:5.9px;line-height:8.9px}
  .inner-url{position:absolute;bottom:12px;width:100%;text-align:center;font-size:10px;font-weight:700}
  .why{position:absolute;left:12px;top:16px;width:245px}
  .why .ticks li{font-size:7px;line-height:8.4px}
  .why-brand{position:absolute;left:0;width:100%;top:135px;text-align:center;font-size:36px}
  .why-phone{position:absolute;left:0;width:100%;top:213px;text-align:center;font-size:19px;font-weight:700;color:#444;display:flex;justify-content:center;align-items:center;gap:8px}
</style>
</head>
<body>

<section class="spread spread--outer">
  <div class="panel panel--a green-fill">
    <div class="process">
      <h2>Our Recruitment Process:</h2>
      <p class="intro">By using our service for Permanent Recruitment, you gain access to SwiftTalent's stringent sourcing and screening process:</p>
      <div class="step"><span class="step__num">1</span><p>Search &amp; Screen: Detailed research and sourcing from our team of consultants. Upon completing a thorough discussion with our clients, we will establish a highly detailed search parameter and utilize our sophisticated HR software, network, database as well as our search methods to identify and contact the most suitable talent for each respective position. All of our targeted candidates will go through SwiftTalent's screening process which may include various interviews and assessments based on our client's requirements.</p></div>
      <div class="step"><span class="step__num">2</span><p>Candidate Shortlist: We understand time is of the utmost importance to our partners. SwiftTalent Consultants aim to not only deliver on the quality of candidates but also on the speed required to meet our client's challenging environment.</p></div>
      <div class="step"><span class="step__num">3</span><p>Client Interview Process: We advise our partners on all the crucial aspects of each candidate prior to the interviews and make sure all the necessary arrangements are met and handled professionally to ensure a seamless interview process from start to finish.</p></div>
      <div class="step"><span class="step__num">4</span><p>Extending an Offer: Our partners expects that each candidate hired can be the best possible match for their organizations. SwiftTalent Consultants is here to minimize the costly mistake of a wrong hire by not only providing a thorough screen and search process, but also conducting thorough reference checks, and upon request, providing documents such as education certificate, proof of employment history, compensation details, etc...</p></div>
      <div class="step"><span class="step__num">5</span><p>Post-Hire: SwiftTalent Consultants aim to grow and develop together with our partners and be your partner of choice for the long-haul. Therefore, we will continue to dedicate our focus on the candidates even after the recruitment is complete to ensure a smooth transition will lead to a long and successful career with our partners.</p></div>
    </div>
    <svg class="photo" style="left:0;top:335px" width="265" height="159" viewBox="0 0 265 159" role="img" aria-label="Photo of business team in a meeting, smiling woman in front">
      <defs><linearGradient id="teamTone" x1="0" x2="1"><stop offset="0" stop-color="#d9cbbd"/><stop offset="1" stop-color="#7b8a99"/></linearGradient></defs>
      <path d="M0 18 Q132 -4 265 22 L265 159 L0 159Z" fill="url(#teamTone)"/>
      <path d="M0 18 Q132 -4 265 22" fill="none" stroke="#fff" stroke-width="3"/>
    </svg>
  </div>

  <div class="panel panel--b grey-fill">
    <div class="contact">
      <h2>Contact us:</h2>
      <div class="rule"></div>
      <div class="contact-item">
        <svg width="9" height="9" viewBox="0 0 10 10"><circle cx="5" cy="5" r="5" fill="#2e9a3c"/><path d="M3.3 2.6l1 1-.5.7c.3.6.8 1.1 1.4 1.4l.7-.5 1 1-.6.8C4.5 7 3 5.5 2.5 3.2z" fill="#fff"/></svg>
        0100-555-246
      </div>
      <div class="contact-item">
        <svg width="9" height="9" viewBox="0 0 10 10"><circle cx="5" cy="5" r="5" fill="#2e9a3c"/><circle cx="5" cy="5" r="2.8" fill="none" stroke="#fff" stroke-width=".8"/><path d="M2.2 5h5.6M5 2.2v5.6" stroke="#fff" stroke-width=".6"/></svg>
        www.swifttalent.com
      </div>
      <div class="contact-item">
        <svg width="9" height="9" viewBox="0 0 10 10"><circle cx="5" cy="5" r="5" fill="#2e9a3c"/><rect x="2.5" y="3.2" width="5" height="3.6" fill="none" stroke="#fff" stroke-width=".7"/><path d="M2.5 3.2L5 5.2 7.5 3.2" fill="none" stroke="#fff" stroke-width=".7"/></svg>
        info@swifttalentmail.com
      </div>
    </div>
    <div class="brand" style="position:absolute;left:68px;top:390px;font-size:26px">SwiftTalent<span>Consultants</span></div>
    <p class="address">3F.,no.18,ln.210,maple Rd.,north Dist.,<br>Harbor City 204,taiwan(r.o.c)</p>
  </div>

  <div class="panel panel--c">
    <div class="brand" style="position:absolute;left:40px;top:22px;font-size:34px">SwiftTalent<span>Consultants</span></div>
    <svg style="position:absolute;left:0;top:90px" width="266" height="404" viewBox="0 0 266 404">
      <path d="M0 305 Q120 345 266 290 L266 404 L0 404Z" fill="var(--green)"/>
      <circle cx="180" cy="175" r="168" fill="none" stroke="var(--green)" stroke-width="6"/>
    </svg>
    <svg class="photo" style="left:0;top:90px" width="266" height="330" viewBox="0 0 266 330" role="img" aria-label="Photo of a smiling businessman shaking hands with a woman across an office desk">
      <defs><linearGradient id="handTone" x1="0" x2="1" y1="0" y2="1"><stop offset="0" stop-color="#d8dde2"/><stop offset=".55" stop-color="#b7a8b8"/><stop offset="1" stop-color="#7f9bb5"/></linearGradient></defs>
      <circle cx="180" cy="175" r="164" fill="url(#handTone)"/>
    </svg>
    <p class="cover-url">www.swifttalent.com</p>
  </div>
</section>

<section class="spread spread--inner">
  <div class="panel panel--a">
    <div class="company small">
      <span class="tag">Our Company</span>
      <p>SwiftTalent Consultants is an esteemed provider of HR solutions in Asia. We have worked closely with our partners from all corners of the world to connect them with the most valuable commodity of all: Talent.</p>
      <p>By offering a broad range of service categories in Contract Staffing &amp; Permanent Placement from various levels of talent and across multiple industries, SwiftTalent Consultants has become a highly-trusted partner for our partners in the region.</p>
      <p>With our team of experienced consultants in your respective field, coupled with our extensive network, sophisticated internal HR platform and diligent screening process, we are able to achieve excellence and deliver effectively and efficiently for our client's most critical HR needs.</p>
      <p>We understand that the only thing consistent in the business world is change. SwiftTalent strives to be the leader in forging that change by increasing your flexibility, reduce time and resources spent on recruitment so you can focus on what your business does best. Our consultants are highly specialized in their sectors in order to provide the highest level of service and commitment to positions ranging from specialized professionals skills to those requiring strong leadership &amp; management experience.</p>
      <p>By offering both Permanent Hire as well as Contract Staffing, our clients have the option of recruiting and retaining the best available talent long term or the flexibility of meeting their needs for a shorter term &amp; project based solution. In providing the complete package of HR services, SwiftTalent believes we can become your trusted partner and together meet your business challenges armed with the confidence and support you need.</p>
      <span class="tag" style="margin-top:3px">Services:</span>
      <ul class="ticks">
        <li>Contract Staffing</li>
        <li>Permanent Recruitment for General &amp; Specialized positions</li>
        <li>Contract to Hire</li>
        <li>Project Recruitment</li>
        <li>Outsourcing / RPO</li>
        <li>Management to Executive Level Recruitment</li>
      </ul>
    </div>
    <div class="photo" style="left:0;top:358px;width:265px;height:133px;background:linear-gradient(90deg,#cfd6dc,#8a8f98 40%,#c4b7ad 70%,#5d6670)" role="img" aria-label="Photo of a group of smiling business people in suits"></div>
  </div>

  <div class="panel panel--b green-fill">
    <div class="industry">
      <h2 class="heading">Industry Coverage:</h2>
      <p class="intro small">Our goal is to become the go-to solution provider for your HR needs in each of our partners. SwiftTalent Consultants is driven to become the industry leader by ensuring our consultants are highly trained to meet our partner's goals in a highly demanding global environment.</p>
      <div class="cols">
        <div class="col">
          <h3>Semiconductor:</h3>
          <ul><li>Foundries and DRAM Fabs</li><li>IC Design Houses</li><li>Equipment / Sub-systems, Frontend</li><li>Chemicals / Materials, Frontend</li><li>EDA Vendor / IP Company</li><li>Test &amp; Assembly Houses</li><li>Equipment, Backend</li><li>Chemicals / Materials, Backend</li></ul>
          <h3>Electronics/TFT-LCD:</h3>
          <ul><li>ICs and Passive Components</li><li>Electronic Components</li><li>Electronic Peripherals / Software</li><li>Electronic Chemicals</li><li>LED</li><li>PCB &amp; SMT</li><li>System (OEM / Contract Manufacturer)</li><li>Electronic Products / Systems</li><li>Test / Measurement Instrument</li></ul>
          <h3>Consumer:</h3>
          <ul><li>FMCG / Consumer Products</li><li>Retail</li><li>Distributors</li><li>Media &amp; Entertainment</li><li>Market Research</li><li>Hospitality</li><li>MLM</li><li>Advertising / PR</li></ul>
          <h3>Banking / Financial:</h3>
          <ul><li>Credit Cards</li><li>Consumer / Retail Banking</li><li>Private Banking / Wealth Management</li><li>Corporate / Investment Banking</li><li>Securities / Fund</li><li>Bonds / Bills</li><li>Asset Management</li></ul>
        </div>
        <div class="col">
          <h3>Healthcare:</h3>
          <ul><li>Pharmaceutical</li><li>Medical Equipment</li><li>Medical Device</li><li>Biotechnology / Bioscience</li><li>CRO</li><li>Hospitals</li><li>Research Institutes</li><li>Distributors</li><li>Animal Health</li><li>Health Information Services</li></ul>
          <h3>IT / Telecom:</h3>
          <ul><li>IT Products and Systems</li><li>IT Software &amp; Data</li><li>System Integration / Consulting Firm</li><li>Mobile Software / Apps &amp; Platforms</li><li>Internet / Services</li><li>Telecom Products and Systems</li><li>Telecom Operators</li><li>Telecom Software</li></ul>
          <h3>Insurance:</h3>
          <ul><li>Life Insurance</li><li>Non-Life Insurance</li></ul>
          <h3>Industrial / Solar:</h3>
          <ul><li>Industrial Products</li><li>Engineering &amp; Construction</li><li>Energy / Utilities</li><li>Chemicals / Materials /</li><li>Metals</li><li>Transportation</li><li>Aviation / Aerospace</li><li>Agriculture</li><li>Automotive</li><li>Textile</li></ul>
        </div>
      </div>
    </div>
    <p class="inner-url">www.swifttalent.com</p>
  </div>

  <div class="panel panel--c grey-fill">
    <div class="why">
      <span class="tag">Why Use SwiftTalent?</span>
      <ul class="ticks">
        <li>Reduce Hiring Risks</li>
        <li>Increase Flexibility</li>
        <li>Gain Access to Top Talent</li>
        <li>Professional Sourcing and Screening Process</li>
        <li>Speed: Save Time and Resources</li>
        <li>Short Turnaround, replenish your talent needs quickly (Contract Staffing)</li>
        <li>Manage Uncertainty (Contract Staffing)</li>
        <li>Our Track Record with Global Organizations</li>
      </ul>
    </div>
    <div class="brand why-brand">SwiftTalent<span style="text-align:center;margin-top:2px">Consultants</span></div>
    <div style="position:absolute;left:36px;top:205px;width:196px;height:1px;background:var(--green)"></div>
    <div class="why-phone">
      <svg width="16" height="16" viewBox="0 0 16 16"><rect width="16" height="16" rx="3" fill="#444"/><path d="M5 3.5l1.6 1.6-.8 1.1c.5 1 1.3 1.8 2.3 2.3l1.1-.8 1.6 1.6-1 1.3C6.8 10.4 4.6 8.2 3.9 4.6z" fill="#fff"/></svg>
      0100-555-246
    </div>
    <div class="photo" style="left:0;top:274px;width:266px;height:217px;background:linear-gradient(90deg,#e9ecef,#c9b79f 45%,#a9b8c6 75%,#e2e5e8)" role="img" aria-label="Photo of a smiling businesswoman giving a thumbs up with colleagues behind her"></div>
  </div>
</section>

</body>
</html>
```